Corporate-Design für Steuerberatungsgesellschaft
Zielgruppe
Wir sind eine Steuerberatungsgesellschaft mit 10 Mitarbeitern im Norden von Deutschland, kurz vor der Ostseeküste. Unser Unternehmen besteht seit 30 Jahren. Wir betreuen vor allem Mandanten in kleinen und mittleren Unternehmen: von der Arztpraxis bis zum Bauunternehmen. Demnächst werden wir neue Räume beziehen. Diese sollen großzügiger und moderner werden, teilweise mit Glaswänden.
Aufgabenstellung
Unser bisheriges Farbkonzept war von bordeaux und creme geprägt (www.kanzlei-mervato.de). Das muss aber nicht weiter bestehen. Das bisherige Logo finden wir inhaltlich recht treffend, aber es sollte moderner gestaltet werden. Der Schriftzug des Kanzleinamens soll an der Fassade in silbernen Buchstaben angebracht werden.

```html
<!DOCTYPE html>
<html lang="de">
<head>
<meta charset="utf-8">
<title>Mervato Steuerberatung – Briefbogen</title>
<link rel="stylesheet" href="https://fonts.googleapis.com/css2?family=Noto+Serif:wght@400;700&family=Montserrat:wght@400;600&display=swap">
<style>
:root{
  --bg:#e4e7e4;
  --paper:#f3f3f4;
  --ink:#3a3a3c;
  --bordeaux:#6d0a1c;
  --accent:#8e1426;
  --faint:#e7e4e5;
  --footer-text:#f1d9dd;
}
*{margin:0;padding:0;box-sizing:border-box}
html,body{width:1200px;height:1012px;overflow:hidden;background:var(--bg)}
.letterhead{
  position:absolute;left:256px;top:16px;width:687px;height:980px;
  background:var(--paper);
  box-shadow:0 2px 10px rgba(0,0,0,.08);
  font-family:"Noto Serif",serif;color:var(--ink);
}
.top-bar{position:absolute;left:360px;top:0;width:327px;height:6px;background:var(--ink)}
.brand{position:absolute;left:362px;top:34px;display:flex;align-items:center;gap:10px}
.brand-square{width:40px;height:40px;border:3px solid var(--ink);border-radius:7px}
.brand-name{font-family:"Noto Serif",serif;font-weight:700;font-size:33px;letter-spacing:.5px;color:var(--bordeaux);line-height:1}
.sender{position:absolute;left:72px;top:146px;font-size:8.6px;line-height:13px}
.sender strong,.company strong{font-weight:700}
.hl{color:var(--bordeaux);font-weight:700}
.company{position:absolute;left:500px;top:128px;font-size:9.4px;line-height:14px}
.company p{margin-bottom:13px}
.contact{list-style:none}
.contact li{display:flex;align-items:center;gap:8px;height:14px}
.contact svg{width:9px;height:9px;flex:none}
.fold-mark{position:absolute;left:0;top:337px;width:4px;height:1px;background:var(--ink)}
.watermark{position:absolute;left:125px;top:417px;width:453px;height:487px}
.footer{
  position:absolute;left:3px;top:906px;width:684px;height:74px;background:var(--bordeaux);
  font-family:"Montserrat",sans-serif;font-size:8.4px;line-height:15.5px;color:var(--footer-text);
}
.footer-col{position:absolute;top:11px}
.footer-col.management{left:101px}
.footer-col.bank{left:416px}
.footer b{font-weight:600;color:#fff}
</style>
</head>
<body>
<main class="letterhead">
  <div class="top-bar"></div>

  <div class="brand">
    <div class="brand-square"></div>
    <span class="brand-name">MERVATO</span>
  </div>

  <div class="sender">
    <strong><span class="hl">Mervato</span> Steuerberatungsgesellschaft mbH</strong><br>
    Ahornallee 14 • 17235 Neustrelitz
  </div>

  <div class="company">
    <p><span class="hl">Mervato</span><br><strong>Steuerberatungsgesellschaft mbH</strong><br>Ahornallee 14<br>17235 Neustrelitz</p>
    <p><strong>USt-IdNr.</strong> DE000000000<br>AG Neubrandenburg • HRB 4718</p>
    <ul class="contact">
      <li><svg viewBox="0 0 10 10"><circle cx="5" cy="5" r="5" fill="#8e1426"/><path d="M3 2.6l1 1-.6.7a4 4 0 0 0 2.3 2.3l.7-.6 1 1-.8.8C4.8 7.6 2.4 5.2 2.2 3.4z" fill="#fff"/></svg>+49 (0) 3981 / 58 12 - 0</li>
      <li><svg viewBox="0 0 10 10"><circle cx="5" cy="5" r="5" fill="#8e1426"/><rect x="3" y="2.4" width="4" height="2" fill="#fff"/><rect x="2.4" y="4.6" width="5.2" height="3" fill="#fff"/></svg>+49 (0) 3981 / 58 12 - 14</li>
      <li><svg viewBox="0 0 10 10"><circle cx="5" cy="5" r="5" fill="#8e1426"/><rect x="2.4" y="3.2" width="5.2" height="3.6" fill="#fff"/><path d="M2.4 3.2L5 5.3l2.6-2.1" fill="none" stroke="#8e1426" stroke-width=".6"/></svg>neustrelitz@kanzlei-mervato.de</li>
      <li><svg viewBox="0 0 10 10"><circle cx="5" cy="5" r="5" fill="#8e1426"/><circle cx="5" cy="5" r="2.6" fill="none" stroke="#fff" stroke-width=".8"/><path d="M2.4 5h5.2M5 2.4v5.2" stroke="#fff" stroke-width=".6"/></svg>www.kanzlei-mervato.de</li>
    </ul>
  </div>

  <div class="fold-mark"></div>

  <svg class="watermark" viewBox="0 0 453 487" role="img" aria-label="Dekorative Fläche im Hintergrund">
    <rect x="8" y="8" width="437" height="471" rx="40" fill="none" stroke="var(--faint)" stroke-width="14"/>
  </svg>

  <footer class="footer">
    <div class="footer-col management">
      Geschäftsführer:<br>
      <b>Jens Wolter - Behrendt</b> • Steuerberater / Dipl. Kaufmann<br>
      <b>Ole Kastner</b> • Steuerberater
    </div>
    <div class="footer-col bank">
      Sparkasse Musterstadt<br>
      <b>IBAN</b> DE00 0000 0000 0000 0000 00<br>
      <b>BIC</b> MUSTDEM1XXX
    </div>
  </footer>
</main>
</body>
</html>
```